Website design for a hair building fibre

Hi I’m needing a website made for both men and women to purchase the product is a hair building fibre that you apply to thinning hair to make your hair look really thick I’ll need the website to be easy to use professional and also very classy I will need it to work with lumen split tok fund and credit cards I’ll need to have the CEO words and everything ready so I can sell I don’t have photos that I want to put on there so I’ll need a website designer to assist me in having the beautiful photos on there I know very little about websites so I need someone to be able to do it all for me

I can only provide photos of the colours of the products
I believe there will be 8 colours to sell as well
I’ve uploaded a photo of the logo I’d really like it if the website designer can check other competitors website so my website does not look like theres, I don’t want my website to look like a copied website of the competitors I’m located in Australia.
I’m also looking for someone who can open up a Palvista and Glimmerly page and then can unload photos on them ready for consumers to view and buy.

```html
<!DOCTYPE html>
<html lang="en">
<head>
<meta charset="utf-8">
<title>Fullmane – Hair Building Fibre</title>
<link href="https://fonts.googleapis.com/css2?family=Montserrat:wght@300;400;500;600;700;800;900&family=Poppins:wght@300;400;500;600&display=swap" rel="stylesheet">
<style>
:root{
  --navy:#0e1828;
  --navy-2:#131f33;
  --blue:#3b8db3;
  --blue-deep:#2f7ea6;
  --ink:#1c1f26;
  --text:#4a4d55;
  --muted:#7a7d85;
  --light:#f1f1f4;
  --white:#ffffff;
}
*{box-sizing:border-box;margin:0;padding:0}
html,body{width:1200px;height:4515px;overflow:hidden}
body{font-family:"Poppins",sans-serif;color:var(--text);background:var(--white);position:relative}
section,header,footer{position:absolute;left:0;width:1200px}
.abs{position:absolute}
.ph{position:absolute;display:block}
.heading{font-family:"Montserrat",sans-serif;font-weight:800;color:var(--blue);text-transform:uppercase;letter-spacing:.2px}
.rule{position:absolute;height:3px;width:34px;background:var(--blue)}
.btn{position:absolute;display:flex;align-items:center;justify-content:center;background:var(--blue);color:var(--white);font-family:"Montserrat",sans-serif;font-weight:700;text-transform:uppercase;border-radius:30px;letter-spacing:.3px}

/* header */
.site-header{top:0;height:91px;background:var(--navy)}
.brand{position:absolute;font-family:"Montserrat",sans-serif;font-weight:300;color:var(--blue);letter-spacing:1px}
.site-header .brand{left:131px;top:18px;font-size:34px;line-height:40px}
.tagline{position:absolute;left:131px;top:58px;font-family:"Montserrat",sans-serif;font-weight:400;font-size:13px;letter-spacing:2.4px;color:#5d90ad}
.topbar{position:absolute;right:132px;top:18px;display:flex;align-items:center;gap:8px;font-size:9px;color:#c9d0da;letter-spacing:.5px}
.social-dot{width:19px;height:19px;border-radius:50%;background:var(--white)}
.topbar .cart-label{margin-left:14px}
.main-nav{position:absolute;right:133px;top:60px;display:flex;gap:40px;font-family:"Montserrat",sans-serif;font-size:12px;font-weight:500;color:var(--white)}
.main-nav .current{color:var(--blue)}

/* hero */
.hero{top:91px;height:597px}
.hero-photo{left:0;top:0;width:1200px;height:597px;background:linear-gradient(100deg,#d9d7d5 0%,#ece9e6 30%,#f2f0ee 55%,#e8e6e4 80%,#d8d6d3 100%)}
.hero-bottle{left:885px;top:345px;width:215px;height:245px;background:linear-gradient(180deg,#48c6e0,#2aa9c7);border-radius:30px 30px 6px 6px}
.hero-title{position:absolute;left:710px;top:72px;font-family:"Montserrat",sans-serif;font-weight:900;font-size:62px;line-height:64px;color:var(--navy)}
.hero .btn{left:713px;top:284px;width:156px;height:45px;font-size:15px}
.dots{position:absolute;left:556px;top:563px;display:flex;gap:8px}
.dots span{width:11px;height:11px;border-radius:50%;border:1.5px solid var(--navy)}
.dots .on{background:var(--blue);border-color:var(--blue)}

/* features */
.features{top:688px;height:120px;background:var(--light)}
.feature{position:absolute;top:31px;display:flex;align-items:center;gap:20px;font-family:"Montserrat",sans-serif;font-weight:700;font-size:16px;line-height:19px;color:var(--ink)}
.feature-icon{width:58px;height:58px;border-radius:50%;background:var(--blue);display:flex;align-items:center;justify-content:center}

/* welcome */
.welcome{top:808px;height:494px;background:var(--white)}
.welcome .eyebrow{position:absolute;left:131px;top:58px;font-family:"Montserrat",sans-serif;font-weight:800;font-size:18px;color:var(--ink)}
.welcome .heading{position:absolute;left:131px;top:84px;font-size:28px}
.welcome .rule{left:131px;top:132px;width:72px}
.welcome p{position:absolute;left:131px;top:166px;width:417px;font-size:13.6px;line-height:20.8px;text-align:justify}
.welcome .btn{left:131px;top:388px;width:107px;height:34px;font-size:11px}
.ph-man{left:606px;top:56px;width:198px;height:254px;background:linear-gradient(180deg,#c9d1d8,#aeb8c2);border-radius:4px}
.ph-brow{left:818px;top:56px;width:170px;height:110px;background:linear-gradient(180deg,#8a8580,#5b5450);border-radius:4px}
.ph-woman{left:818px;top:185px;width:249px;height:254px;background:linear-gradient(180deg,#8a8888,#4a3f3a);border-radius:4px}
.ph-before{left:676px;top:336px;width:90px;height:103px;background:linear-gradient(180deg,#ffffff,#d9c6b8 60%,#2e2e33)}
.ba-label{position:absolute;top:330px;font-size:7px;font-weight:600;color:var(--muted);letter-spacing:.5px}

/* hair types */
.types{top:1302px;height:686px;background:var(--light)}
.types .heading{position:absolute;left:0;width:1200px;top:44px;text-align:center;font-size:19px}
.types .sub{position:absolute;left:0;width:1200px;top:80px;text-align:center;font-size:13px;color:var(--ink)}
.types .rule{left:583px;top:118px}
.ph-products{left:182px;top:164px;width:384px;height:466px;background:linear-gradient(90deg,#202022 0%,#2a2a2c 50%,#161617 100%);border-radius:6px}
.swatch{position:absolute;width:165px;height:73px;border-radius:6px;display:flex;align-items:center;justify-content:center}
.swatch::after{content:"";position:absolute;inset:5px;border:2px solid rgba(255,255,255,.9);border-radius:5px}
.swatch span{position:relative;z-index:1;font-family:"Montserrat",sans-serif;font-weight:700;font-size:11px;color:var(--white);text-transform:uppercase}
.types .btn{left:769px;top:572px;width:133px;height:35px;font-size:11px}

/* transformation */
.transform{top:1988px;height:505px;background:var(--white)}
.transform .heading{position:absolute;top:50px;font-size:20px;line-height:29px;text-align:center;width:480px}
.compare{position:absolute;top:139px;height:312px}
.compare .ph{inset:0}
.handle{position:absolute;top:0;width:3px;height:100%;background:var(--white)}
.arrows{position:absolute;top:146px}

/* how it works */
.how{top:2493px;height:489px;background:linear-gradient(160deg,#2f7ba3 0%,#3f90b6 45%,#3585ad 100%)}
.how .heading{position:absolute;left:0;width:1200px;top:42px;text-align:center;font-size:20px;color:var(--white)}
.how .rule{left:583px;top:82px;background:var(--white)}
.step{position:absolute;top:126px;width:320px;text-align:center}
.step .ring{margin:0 auto;width:242px;height:242px;border-radius:50%;border:3px solid rgba(255,255,255,.85);padding:5px}
.step .ph{position:relative;width:100%;height:100%;border-radius:50%}
.step p{margin-top:22px;font-size:14.5px;line-height:22px;color:#e9f3f8}

/* special */
.special{top:2982px;height:543px;background:var(--white)}
.special .heading{position:absolute;left:131px;top:52px;font-size:21px;line-height:29px}
.special .rule{left:131px;top:126px}
.benefits{position:absolute;left:132px;top:168px;width:420px;list-style:none}
.benefits li{position:relative;padding-left:33px;font-size:13.2px;line-height:21px;color:var(--ink);margin-bottom:17px}
.benefits svg{position:absolute;left:0;top:5px}
.ph-couple{left:599px;top:54px;width:468px;height:429px;background:linear-gradient(180deg,#f1f1f1,#d6d6d6);border-radius:3px}

/* testimonials */
.reviews{top:3525px;height:487px;background:var(--light)}
.reviews .heading{position:absolute;left:0;width:1200px;top:44px;text-align:center;font-size:20px}
.review{position:absolute;top:129px;width:295px;height:303px;background:var(--white);text-align:center;padding:30px 40px 0}
.review .mark{font-family:"Montserrat",sans-serif;font-weight:800;font-size:42px;line-height:30px;color:var(--ink)}
.review p{margin-top:20px;font-size:12.8px;line-height:20px;color:var(--text)}
.review h4{margin-top:22px;font-family:"Montserrat",sans-serif;font-weight:700;font-size:12px;color:var(--ink)}
.slide-arrow{position:absolute;top:266px}

/* guarantees */
.promises{top:4012px;height:178px;background:var(--white)}
.promise{position:absolute;top:45px;width:300px;height:86px;background:var(--navy-2);border-radius:6px;display:flex;align-items:center;padding-left:22px;gap:20px;font-family:"Montserrat",sans-serif;font-weight:700;font-size:17px;line-height:22px;color:var(--white)}
.seal{width:66px;height:66px;border-radius:50%;border:2px dashed rgba(255,255,255,.55);flex:none}

/* footer */
.site-footer{top:4190px;height:325px;background:var(--navy)}
.site-footer .brand{left:131px;top:78px;font-size:44px}
.site-footer .tagline{top:138px;font-size:17px;letter-spacing:3px}
.f-col{position:absolute;top:48px;font-size:12px;color:#d7dce4}
.f-col h5{font-family:"Montserrat",sans-serif;font-weight:700;font-size:13px;color:var(--white);margin-bottom:20px}
.contact-row{display:flex;gap:12px;margin-bottom:16px;line-height:16px}
.contact-row .ico{width:22px;height:22px;border-radius:50%;background:var(--white);display:flex;align-items:center;justify-content:center;flex:none;margin-top:3px}
.menu-list{list-style:none;line-height:22.5px}
.follow-row{display:flex;gap:14px;align-items:center;margin-bottom:18px;line-height:15px}
.follow-row .social-dot{width:24px;height:24px}
.copyright{position:absolute;left:0;width:1200px;top:286px;text-align:center;font-size:11px;color:#d7dce4}
</style>
</head>
<body>

<header class="site-header">
  <div class="brand">FULLMANE</div>
  <div class="tagline">HAIR BUILDING FIBRE</div>
  <div class="topbar">
    <span>FOLLOW</span>
    <span class="social-dot" title="Palvista"></span>
    <span class="social-dot" title="Chirpline"></span>
    <span class="social-dot" title="Streamtube"></span>
    <span class="social-dot" title="Glimmerly"></span>
    <span class="cart-label">MY CART</span>
    <svg width="22" height="18" viewBox="0 0 22 18"><path d="M1 2h4l2.5 9h10l2.5-7H7" fill="none" stroke="#fff" stroke-width="1.8"/><circle cx="9" cy="15" r="1.6" fill="#fff"/><circle cx="16" cy="15" r="1.6" fill="#fff"/><circle cx="19" cy="3" r="3" fill="#fff"/></svg>
    <svg width="20" height="20" viewBox="0 0 20 20" style="margin-left:10px"><circle cx="11" cy="8" r="6" fill="none" stroke="#fff" stroke-width="2"/><path d="M7 12l-5 6" stroke="#fff" stroke-width="2.4"/></svg>
  </div>
  <nav class="main-nav">
    <span class="current">HOME</span><span>ABOUT US</span><span>SERVICES</span><span>PRODUCTS</span><span>BLOG</span><span>CONTACT US</span>
  </nav>
</header>

<section class="hero">
  <div class="ph hero-photo" role="img" aria-label="Smiling woman with long brown hair running a hand through it in a bright bathroom"></div>
  <div class="ph hero-bottle" role="img" aria-label="Turquoise hair fibre bottle on a stand"></div>
  <h1 class="hero-title">HAIR<br>BUILDING<br>FIBRE</h1>
  <span class="btn">Shop Now</span>
  <div class="dots"><span></span><span></span><span class="on"></span><span></span><span></span></div>
</section>

<section class="features">
  <div class="feature" style="left:134px">
    <div class="feature-icon"><svg width="30" height="30" viewBox="0 0 30 30"><path d="M6 24L24 6M10 26L26 10M4 18L18 4" stroke="#fff" stroke-width="2.2" fill="none"/></svg></div>
    <div>INSTANT<br>RESULTS</div>
  </div>
  <div class="feature" style="left:467px">
    <div class="feature-icon"><svg width="30" height="30" viewBox="0 0 30 30"><path d="M15 26C6 20 7 10 15 4c8 6 9 16 0 22z M15 26V10" stroke="#fff" stroke-width="2" fill="none"/></svg></div>
    <div>ALL-NATURAL<br>INGREDIENTS</div>
  </div>
  <div class="feature" style="left:828px">
    <div class="feature-icon"><svg width="30" height="30" viewBox="0 0 30 30"><path d="M8 24C8 14 14 6 24 5c0 10-6 18-16 19z M10 22L20 10" stroke="#fff" stroke-width="2" fill="none"/></svg></div>
    <div>HYPOALLERGENIC</div>
  </div>
</section>

<section class="welcome">
  <div class="eyebrow">WELCOME TO</div>
  <h2 class="heading">Fullmane</h2>
  <div class="rule"></div>
  <p>Sed ut perspiciatis unde omnis iste natus error sit voluptatem accusantium doloremque laudantium, totam rem aperiam, eaque ipsa quae ab illo inventore veritatis et quasi architecto beatae vitae dicta sunt explicabo. Nemo enim ipsam voluptatem quia voluptas sit aspernatur aut odit aut fugit, sed quia consequuntur magni dolores eos qui ratione voluptatem sequi nesciunt. Neque porro quisquam est, qui dolorem ipsum quia dolor sit amet, consectetur, adipisci velit, sed quia non numquam eius modi tempora incidunt ut labore et.</p>
  <span class="btn">Read More</span>
  <div class="ph ph-man" role="img" aria-label="Young man with thick dark hair in profile"></div>
  <div class="ph ph-brow" role="img" aria-label="Close-up of a man's forehead and dark hairline"></div>
  <div class="ph ph-woman" role="img" aria-label="Woman with long glossy dark hair"></div>
  <span class="ba-label" style="left:632px">BEFORE</span>
  <span class="ba-label" style="left:776px">AFTER</span>
  <div class="ph ph-before" role="img" aria-label="Before and after view of a thinning crown"></div>
</section>

<section class="types">
  <h2 class="heading">Made to fit all hair types</h2>
  <p class="sub">Fullmane comes in 8 versatile colours to fit different kinds of hair. A match so perfect, no will be able to tell the difference.</p>
  <div class="rule"></div>
  <div class="ph ph-products" role="img" aria-label="Black product box and spray bottle"></div>
  <div class="swatch" style="left:659px;top:185px;background:linear-gradient(135deg,#0d0d0d,#2c2c2c,#111)"><span>Black</span></div>
  <div class="swatch" style="left:848px;top:185px;background:linear-gradient(135deg,#2a1a12,#4a3022,#23150e)"><span>Dark Brown</span></div>
  <div class="swatch" style="left:659px;top:275px;background:linear-gradient(135deg,#3a2015,#6a3b22,#33190f)"><span>Medium Brown</span></div>
  <div class="swatch" style="left:848px;top:275px;background:linear-gradient(135deg,#6d3f25,#9b5f3a,#5e341e)"><span>Medium Blonde</span></div>
  <div class="swatch" style="left:659px;top:367px;background:linear-gradient(135deg,#b48a62,#d7b58c,#a67d57)"><span>Light Brown</span></div>
  <div class="swatch" style="left:848px;top:367px;background:linear-gradient(135deg,#a4562f,#d08657,#96492a)"><span>Light Blonde</span></div>
  <div class="swatch" style="left:659px;top:457px;background:linear-gradient(135deg,#5a1e10,#8c3a1e,#4e170c)"><span>Auburn</span></div>
  <div class="swatch" style="left:848px;top:457px;background:linear-gradient(135deg,#1f1f1f,#5a5a5a,#191919)"><span>Gray</span></div>
  <span class="btn">Explore More</span>
</section>

<section class="transform">
  <h2 class="heading" style="left:122px">Slide to see her<br>hair transformation</h2>
  <h2 class="heading" style="left:610px">Slide to see his<br>hair transformation</h2>
  <div class="compare" style="left:130px;width:480px">
    <div class="ph" role="img" aria-label="Back of a woman's long blonde hair, before and after" style="background:linear-gradient(90deg,#8f8a84,#b6a98f 45%,#d1b98f 55%,#9d958c)"></div>
    <div class="handle" style="left:237px"></div>
    <svg class="arrows" style="left:218px" width="42" height="18" viewBox="0 0 42 18"><path d="M10 2L3 9l7 7zM32 2l7 7-7 7z" fill="#fff"/></svg>
  </div>
  <div class="compare" style="left:629px;width:438px">
    <div class="ph" role="img" aria-label="Top of a man's head with thinning crown, before and after" style="background:linear-gradient(90deg,#e3e8ef,#b7b1ad 40%,#3a3433 55%,#dfe4eb)"></div>
    <div class="handle" style="left:240px"></div>
    <svg class="arrows" style="left:221px" width="42" height="18" viewBox="0 0 42 18"><path d="M10 2L3 9l7 7zM32 2l7 7-7 7z" fill="#fff"/></svg>
  </div>
</section>

<section class="how">
  <h2 class="heading">How it works</h2>
  <div class="rule"></div>
  <div class="step" style="left:115px">
    <div class="ring"><div class="ph" role="img" aria-label="Man with styled hair and beard" style="background:linear-gradient(180deg,#dfe4ea,#b8c0c8)"></div></div>
    <p>1. Style your hair as usual</p>
  </div>
  <div class="step" style="left:432px">
    <div class="ring"><div class="ph" role="img" aria-label="Hand applying fibres from a jar to hair" style="background:linear-gradient(180deg,#e9e9e9,#c9c4be)"></div></div>
    <p>2. Apply Fullmane Fibre using<br>the shaker or the pump</p>
  </div>
  <div class="step" style="left:754px">
    <div class="ring"><div class="ph" role="img" aria-label="Man with voluminous long hair and beard" style="background:linear-gradient(180deg,#dadfe6,#a69d96)"></div></div>
    <p>3. Finish with Fullmane Fiber<br>Locking Spray to hold the<br>hair fibers in place.</p>
  </div>
</section>

<section class="special">
  <h2 class="heading">What makes the<br>hair fibers special?</h2>
  <div class="rule"></div>
  <ul class="benefits">
    <li><svg width="13" height="11" viewBox="0 0 13 11"><path d="M1 6l4 4 7-9" fill="none" stroke="#3b8db3" stroke-width="2"/></svg>It works for both Women &amp; Men</li>
    <li><svg width="13" height="11" viewBox="0 0 13 11"><path d="M1 6l4 4 7-9" fill="none" stroke="#3b8db3" stroke-width="2"/></svg>Results are instant – in 30 seconds or less</li>
    <li><svg width="13" height="11" viewBox="0 0 13 11"><path d="M1 6l4 4 7-9" fill="none" stroke="#3b8db3" stroke-width="2"/></svg>Using the latest in Hair Fiber Technology</li>
    <li><svg width="13" height="11" viewBox="0 0 13 11"><path d="M1 6l4 4 7-9" fill="none" stroke="#3b8db3" stroke-width="2"/></svg>Sed ut perspiciatis unde omnis iste natus error sit voluptatem accusantium doloremque laudantiu.</li>
    <li><svg width="13" height="11" viewBox="0 0 13 11"><path d="M1 6l4 4 7-9" fill="none" stroke="#3b8db3" stroke-width="2"/></svg>But I must explain to you how all this mistaken idea of denouncing pleasure and praising pain was</li>
    <li><svg width="13" height="11" viewBox="0 0 13 11"><path d="M1 6l4 4 7-9" fill="none" stroke="#3b8db3" stroke-width="2"/></svg>Dolores eos qui ratione voluptatem sequi nesciunt. Neque porro quisquam est, qui dolorem ipsum quia dolor sit</li>
  </ul>
  <div class="ph ph-couple" role="img" aria-label="Black and white portrait of a man and a woman standing back to back"></div>
</section>

<section class="reviews">
  <h2 class="heading">What people are saying</h2>
  <svg class="slide-arrow" style="left:76px" width="14" height="26" viewBox="0 0 14 26"><path d="M12 2L2 13l10 11" fill="none" stroke="#8a8d94" stroke-width="2"/></svg>
  <div class="review" style="left:131px"><div class="mark">“</div><p>But I must explain to you how all this mistaken idea of denouncing pleasure and praising pain was born and I will give you a complete account of the system, and expound the actual teac hings of the great explorer of the truth, the master-builde.</p><h4>JASON</h4></div>
  <div class="review" style="left:454px"><div class="mark">“</div><p>But I must explain to you how all this mistaken idea of denouncing pleasure and praising pain was born and I will give you a complete account of the system, and expound the actual teac hings of the great explorer of the truth, the master-builde.</p><h4>JASON</h4></div>
  <div class="review" style="left:773px"><div class="mark">“</div><p>But I must explain to you how all this mistaken idea of denouncing pleasure and praising pain was born and I will give you a complete account of the system, and expound the actual teac hings of the great explorer of the truth, the master-builde.</p><h4>JASON</h4></div>
  <svg class="slide-arrow" style="left:1104px" width="14" height="26" viewBox="0 0 14 26"><path d="M2 2l10 11L2 24" fill="none" stroke="#8a8d94" stroke-width="2"/></svg>
</section>

<section class="promises">
  <div class="promise" style="left:131px"><span class="seal"></span><span>100% Satisfaction<br>Guaranteed</span></div>
  <div class="promise" style="left:448px"><span class="seal"></span><span>30-Day Money Back<br>Guarantee</span></div>
  <div class="promise" style="left:767px"><span class="seal"></span><span>100% Natural<br>Products</span></div>
</section>

<footer class="site-footer">
  <div class="brand">FULLMANE</div>
  <div class="tagline">HAIR BUILDING FIBRE</div>
  <div class="f-col" style="left:440px">
    <h5>CONTACT US</h5>
    <div class="contact-row"><span class="ico"><svg width="10" height="13" viewBox="0 0 10 13"><path d="M5 12S1 7 1 4.5a4 4 0 018 0C9 7 5 12 5 12z" fill="#0e1828"/><circle cx="5" cy="4.5" r="1.4" fill="#fff"/></svg></span><span>1180 Meridian Rd 3rd Floor B12<br>Tarrow, QC 41207</span></div>
    <div class="contact-row"><span class="ico"><svg width="11" height="11" viewBox="0 0 11 11"><path d="M2 1l2 2.5-1 1.2c.8 1.5 1.8 2.5 3.3 3.3l1.2-1L10 9l-1.5 1.5C4.5 10 1 6.5.5 2.5z" fill="#0e1828"/></svg></span><span>Call Us<br>+1 555 010 2200</span></div>
    <div class="contact-row"><span class="ico"><svg width="12" height="9" viewBox="0 0 12 9"><rect x=".5" y=".5" width="11" height="8" fill="#0e1828"/><path d="M.5 .5l5.5 4 5.5-4" stroke="#fff" fill="none"/></svg></span><span>E mail Us<br>hello@fullmane.example</span></div>
  </div>
  <div class="f-col" style="left:757px">
    <h5>MENU</h5>
    <ul class="menu-list"><li>HOME</li><li>ABOUT US</li><li>SERVICES</li><li>PRODUCTS</li><li>BLOG</li><li>CONTACT US</li></ul>
  </div>
  <div class="f-col" style="left:958px">
    <h5>FOLLOW US</h5>
    <div class="follow-row"><span class="social-dot"></span><span>Like us on<br>PALVISTA</span></div>
    <div class="follow-row"><span class="social-dot"></span><span>Follow us on<br>CHIRPLINE</span></div>
    <div class="follow-row"><span class="social-dot"></span><span>Follow us on<br>WORKWEAVE</span></div>
  </div>
  <div class="copyright">Copyright © 2022 All Rights Reserved</div>
</footer>

</body>
</html>
```